TA BRAMLEY BUSINESS CARD DESIGN PROJECT

We need to utilize our logo that was expertly created on PixelHarbor and now need to match this with a business card design.

```html
<!DOCTYPE html>
<html lang="en">
<head>
<meta charset="utf-8">
<title>TA BRAMLEY Business Card</title>
<link rel="stylesheet" href="https://fonts.googleapis.com/css2?family=Montserrat:wght@400;700;800&display=swap">
<style>
  :root {
    --bg: #d6d6d6;
    --card: #f2f2f2;
    --brand-blue: #0a3a9c;
    --ink: #1b1b1b;
  }
  html, body {
    margin: 0;
    padding: 0;
    width: 1200px;
    height: 1051px;
    overflow: hidden;
    background: var(--bg);
    font-family: "Montserrat", sans-serif;
  }
  .canvas {
    position: relative;
    width: 1200px;
    height: 1051px;
  }
  .card {
    position: absolute;
    left: 340px;
    width: 520px;
    height: 297px;
    background: var(--card);
    border-bottom: 5px solid var(--brand-blue);
    box-sizing: border-box;
    box-shadow: 0 12px 30px rgba(0,0,0,0.18);
  }
  .card--front { top: 170px; }
  .card--back { top: 580px; }

  .brand {
    position: absolute;
    inset: 0;
    display: flex;
    align-items: center;
    justify-content: center;
    gap: 18px;
  }
  .brand__dot {
    width: 34px;
    height: 34px;
    border-radius: 50%;
    background: var(--brand-blue);
  }
  .brand__name {
    font-weight: 800;
    font-size: 46px;
    letter-spacing: 8px;
    color: var(--brand-blue);
  }

  .identity {
    position: absolute;
    left: 70px;
    top: 88px;
    width: 170px;
    text-align: right;
  }
  .identity__name {
    font-weight: 700;
    font-size: 17px;
    color: var(--brand-blue);
    letter-spacing: 0.3px;
  }
  .identity__role {
    font-size: 12px;
    color: var(--ink);
    margin-top: 3px;
  }
  .divider {
    position: absolute;
    left: 258px;
    top: 88px;
    width: 1.5px;
    height: 70px;
    background: var(--brand-blue);
  }
  .contacts {
    position: absolute;
    left: 274px;
    top: 92px;
    margin: 0;
    padding: 0;
    list-style: none;
    font-size: 12px;
    color: var(--ink);
  }
  .contacts li {
    display: flex;
    align-items: center;
    gap: 8px;
    height: 21px;
  }
  .contacts svg { width: 11px; height: 11px; fill: var(--brand-blue); }
  .address {
    position: absolute;
    left: 0;
    right: 0;
    bottom: 42px;
    text-align: center;
    font-size: 12px;
    color: var(--ink);
  }
</style>
</head>
<body>
<div class="canvas">
  <section class="card card--front">
    <div class="brand">
      <span class="brand__dot"></span>
      <span class="brand__name">TA BRAMLEY</span>
    </div>
  </section>

  <section class="card card--back">
    <div class="identity">
      <div class="identity__name">CALLUM REEVE</div>
      <div class="identity__role">Managing Director</div>
    </div>
    <div class="divider"></div>
    <ul class="contacts">
      <li>
        <svg viewBox="0 0 24 24"><path d="M6.6 10.8a15.1 15.1 0 0 0 6.6 6.6l2.2-2.2a1 1 0 0 1 1-.25 11.4 11.4 0 0 0 3.6.57 1 1 0 0 1 1 1V20a1 1 0 0 1-1 1A17 17 0 0 1 3 4a1 1 0 0 1 1-1h3.5a1 1 0 0 1 1 1c0 1.25.2 2.45.57 3.6a1 1 0 0 1-.25 1z"/></svg>
        555 018 264
      </li>
      <li>
        <svg viewBox="0 0 24 24"><path d="M2 5h20v14H2z M2 5l10 8 10-8" /></svg>
        hello@tabramley.com
      </li>
      <li>
        <svg viewBox="0 0 24 24"><circle cx="12" cy="12" r="10"/></svg>
        www.tabramley.com
      </li>
    </ul>
    <div class="address">14 Harrow Lane, Easton, Zip 5821</div>
  </section>
</div>
</body>
</html>
```